Pella's Salon (Business Cards) Needed

I need a new business card for my hair salon based in Linden Bay, OR called "Pella's Salon". I have been in business at the same location for the past 15 years, and have recently remodeled the place to be a little bit more upscale and modern. Previously, my clientele's were mostly men, but now I would like to attract more female clientele into my business. I would like the design to attract the female's attention with it's modern touch, flowery, freshness with just enough information and not too compact. Simple, clean and professional is the look.
Requirements
Must Have:
- The design should include:
Business name: Pella's Salon
Hairstylist/Owner Name: Pella Marsden
Phone Number: (555) 418-6307
Website: www.pellahairstudio.example
Address: 48153 Corwin Dale Lane
Linden Bay, OR 20917
FRONT CARD should include:
- Logo (Business name)
- Slogan (Your beauty, our passion)
BACK CARD should include:
- Logo (Business name)
- Hairstyle name
- Phone number
- Website
- Address
Updates
Project Deadline Extended
Reason: There were some good submission for this project, but most of the submission were poorly designed, and did not have what I want. There isn't enough designs for me to choose from and not one of it stood out to me. I would like to extend it a bit longer to see if any other designer would step up to the plate, and deliver. Thank you.
Industry/Entity Type
Hair
Requirements
Must have
- The front side of the business card should only have the business name (Pella's Salon) and slogan, (Your beauty our passion) with a creative design.
The back side of the business card should have all the business information, and creative design that matches with the front, but not identical.
The first letter (V) in (Pella's) should have a flower design connected to it, which blends into the background design.
Nice to have
- Light color scheme.
Should not have
- The front, and back should not have the same design.
Do not include illustrations of a pair of scissors, combs or any objects in the design.
The design should not take the main focus from the business name and business information. It should blend well together... if that's possible.

```html
<!DOCTYPE html>
<html lang="en">
<head>
<meta charset="utf-8">
<title>Pella's Salon — Business Cards</title>
<link rel="stylesheet" href="https://fonts.googleapis.com/css2?family=Open+Sans:wght@400;600;700&family=Montserrat:wght@500&display=swap">
<style>
  :root {
    --backdrop: #e4e4e6;
    --card: #ffffff;
    --brand-blue: #3a4fa8;
    --text-blue: #3d56b0;
    --tag-blue: #3f5bb2;
    --tag-text: #ffffff;
    --photo-dark: #2b2b30;
    --photo-warm: #b88a6a;
    --photo-light: #d9d4cf;
    --bloom-deep: #2f5fd0;
    --bloom-mid: #3fa6e6;
    --bloom-light: #cfeaf8;
    --shadow: rgba(0, 0, 0, 0.18);
  }
  * { box-sizing: border-box; margin: 0; padding: 0; }
  html, body {
    width: 1200px;
    height: 868px;
    overflow: hidden;
    background: var(--backdrop);
  }
  .canvas {
    position: relative;
    width: 1200px;
    height: 868px;
  }
  .card {
    position: absolute;
    top: 279px;
    width: 540px;
    height: 310px;
    background: var(--card);
    border-radius: 26px;
    box-shadow: 0 6px 18px var(--shadow);
    overflow: hidden;
  }
  .card--front { left: 40px; }
  .card--back { left: 620px; }

  /* Front */
  .photo-row {
    position: absolute;
    top: 30px;
    left: 50px;
    display: flex;
    gap: 12px;
  }
  .photo {
    width: 140px;
    height: 140px;
  }
  .photo--man { background: linear-gradient(160deg, var(--photo-light), #bdb7b2); }
  .photo--profile { background: linear-gradient(150deg, var(--photo-dark), var(--photo-warm)); }
  .photo--smile { background: linear-gradient(150deg, #7a5236, #e4c7ae); }

  .logo {
    font-family: "Open Sans", sans-serif;
    font-weight: 700;
    color: var(--brand-blue);
    line-height: 1;
    white-space: nowrap;
  }
  .slogan {
    font-family: "Montserrat", sans-serif;
    font-weight: 500;
    color: var(--text-blue);
    text-transform: uppercase;
    letter-spacing: 0.12em;
    white-space: nowrap;
  }
  .front-brand {
    position: absolute;
    top: 198px;
    left: 250px;
    text-align: center;
  }
  .front-brand .logo { font-size: 26px; }
  .front-brand .slogan { font-size: 8.5px; margin-top: 6px; }

  /* Back */
  .bloom {
    position: absolute;
    inset: 0;
  }
  .name-tag {
    position: absolute;
    top: 96px;
    right: 22px;
    padding: 6px 16px 7px;
    background: var(--tag-blue);
    border-radius: 12px;
    color: var(--tag-text);
    font-family: "Open Sans", sans-serif;
    text-align: center;
    line-height: 1.3;
  }
  .name-tag__name { font-size: 13px; font-weight: 600; }
  .name-tag__role { font-size: 10px; }

  .back-brand {
    position: absolute;
    top: 132px;
    left: 32px;
  }
  .back-brand .logo { font-size: 26px; }
  .back-brand .slogan { font-size: 8px; margin-top: 5px; }

  .contact {
    position: absolute;
    top: 188px;
    left: 34px;
    list-style: none;
    font-family: "Open Sans", sans-serif;
    font-size: 14px;
    color: var(--text-blue);
  }
  .contact__item {
    display: flex;
    align-items: flex-start;
    gap: 10px;
    margin-bottom: 8px;
    line-height: 1.4;
  }
  .contact__item--address { margin-top: 6px; }
  .contact__icon {
    width: 12px;
    height: 12px;
    margin-top: 4px;
    flex: none;
    fill: var(--text-blue);
  }
</style>
</head>
<body>
<main class="canvas">

  <section class="card card--front" aria-label="Front of business card">
    <div class="photo-row">
      <div class="photo photo--man" role="img" aria-label="Photo of a man with a spiky short haircut, side view"></div>
      <div class="photo photo--profile" role="img" aria-label="Photo of a woman with a sleek fringe, profile view"></div>
      <div class="photo photo--smile" role="img" aria-label="Photo of a smiling woman with long wavy hair"></div>
    </div>
    <div class="front-brand">
      <p class="logo">Pella's Salon</p>
      <p class="slogan">Your beauty our passion</p>
    </div>
  </section>

  <section class="card card--back" aria-label="Back of business card">
    <svg class="bloom" viewBox="0 0 540 310" role="img" aria-label="Blue watercolour flower illustration blending into soft swirling lines">
      <defs>
        <linearGradient id="bloomFill" x1="0" y1="1" x2="1" y2="0">
          <stop offset="0" stop-color="var(--bloom-light)" stop-opacity="0.4"/>
          <stop offset="0.5" stop-color="var(--bloom-mid)" stop-opacity="0.85"/>
          <stop offset="1" stop-color="var(--bloom-deep)"/>
        </linearGradient>
      </defs>
      <path d="M0 150 C 80 120, 150 110, 220 90 C 280 70, 320 110, 380 120 C 440 130, 500 110, 540 95 L 540 0 L 180 0 C 200 40, 120 90, 0 120 Z" fill="url(#bloomFill)"/>
    </svg>

    <div class="name-tag">
      <p class="name-tag__name">Pella Marsden</p>
      <p class="name-tag__role">Hairstylist &amp; Owner</p>
    </div>

    <div class="back-brand">
      <p class="logo">Pella's Salon</p>
      <p class="slogan">Your beauty our passion</p>
    </div>

    <ul class="contact">
      <li class="contact__item">
        <svg class="contact__icon" viewBox="0 0 24 24" aria-hidden="true"><path d="M6.6 10.8a15.1 15.1 0 0 0 6.6 6.6l2.2-2.2c.3-.3.7-.4 1-.2 1.1.4 2.3.6 3.6.6.6 0 1 .4 1 1V20c0 .6-.4 1-1 1A17 17 0 0 1 3 4c0-.6.4-1 1-1h3.5c.6 0 1 .4 1 1 0 1.300.2 2.500.6 3.600.1.3 0 .7-.2 1z"/></svg>
        <span>(555) 418-6307</span>
      </li>
      <li class="contact__item">
        <svg class="contact__icon" viewBox="0 0 24 24" aria-hidden="true"><path d="M12 2a10 10 0 1 0 0 20 10 10 0 0 0 0-20zm6.9 6h-2.9a15.6 15.6 0 0 0-1.4-3.6A8 8 0 0 1 18.9 8zM12 4c.8 1.2 1.5 2.5 1.9 4h-3.8c.4-1.5 1.1-2.8 1.9-4zM4.3 14a8 8 0 0 1 0-4h3.4a16 16 0 0 0 0 4zm.8 2h2.9c.3 1.3.8 2.5 1.4 3.6A8 8 0 0 1 5.1 16zM8 8H5.1a8 8 0 0 1 4.3-3.6C8.8 5.5 8.3 6.7 8 8zm4 12c-.8-1.2-1.5-2.5-1.9-4h3.8c-.4 1.5-1.1 2.8-1.900 4zm2.3-6H9.7a14 14 0 0 1 0-4h4.6a14 14 0 0 1 0 4zm.3 5.6c.6-1.1 1.1-2.3 1.4-3.6h2.9a8 8 0 0 1-4.3 3.6zm1.7-5.6a16 16 0 0 0 0-4h3.4a8 8 0 0 1 0 4z"/></svg>
        <span>www.pellahairstudio.example</span>
      </li>
      <li class="contact__item contact__item--address">
        <svg class="contact__icon" viewBox="0 0 24 24" aria-hidden="true"><path d="M12 2a7 7 0 0 0-7 7c0 5.2 7 13 7 13s7-7.8 7-13a7 7 0 0 0-7-7zm0 9.5a2.5 2.5 0 1 1 0-5 2.5 2.5 0 0 1 0 5z"/></svg>
        <span>48153 Corwin Dale Lane<br>Linden Bay, OR 20917</span>
      </li>
    </ul>
  </section>

</main>
</body>
</html>
```